New Fun, Positive, energised looking Business Card Needed for High Achiever Coach

I am looking for a two sided full colour business card. I am self employed and have recently re branded my 1-2-1 work re-vitalising high achievers. My target client base for these cards is therefore high achievers - usually aged 40 -55, they are often entrepreneurs, CEO or work in banking and finance and 2/3 are male. I work with them on 90 day or 6 month coaching programs to help them live their success in a healthier, more sustainable and fulfiiled way. They pay for this privately so though they are corporate types the cards need not look 'corporate'. I want to portray the idea of transformation, vitality and re-connecting.
You can get a feel for the look I like on my new website: morvenlisk.co.uk
I want to use this logo with strapline (Re-Vitalising High Achievers) (I purchased off Logoharbor) and font/ colours (the turquoise and green).
Details to include on the card:
www.morvenlisk.co.uk
+44 7915 302618
morven@morvenlisk.co.uk
skype: morvenlisk
I'd also like to include:
Do you struggle to switch off? Want to be healthier and feel fitter? Want closer relationships? More clarity over the direction you are headed? I can help you do these things using integrated mind-body techniques. Visit morvenlisk.co.uk TODAY to apply for a FREE Breakthrough session.
BUT if that is too much text for a card I am open to advice/ammendments.
Updates
Thanks for your design - I am considering them. PLease change the wording to :

```html
<!DOCTYPE html>
<html lang="en">
<head>
<meta charset="utf-8">
<title>Morven Lisk – Business Card</title>
<link rel="stylesheet" href="https://fonts.googleapis.com/css2?family=Open+Sans:wght@400;600;700&display=swap">
<style>
  :root {
    --backdrop: #e9e9ee;
    --card: #ffffff;
    --turquoise: #0aa3c7;
    --green: #5cb85c;
    --ink: #3a3a3a;
    --rule: #9a9a9a;
  }
  * { margin: 0; padding: 0; box-sizing: border-box; }
  html, body {
    width: 1200px; height: 987px; overflow: hidden;
    background: var(--backdrop);
    font-family: "Open Sans", Arial, sans-serif;
    color: var(--ink);
  }
  .stage { position: relative; width: 1200px; height: 987px; }
  .card {
    position: absolute; left: 220px;
    width: 760px; height: 420px;
    background: var(--card);
    border-radius: 26px;
    overflow: hidden;
    box-shadow: 0 6px 18px rgba(0,0,0,0.12);
  }
  .card--back { top: 50px; }
  .card--front { top: 517px; }

  .brand {
    position: absolute; left: 40px; top: 0;
    width: 300px; height: 100%;
    display: flex; align-items: center; justify-content: center;
    gap: 12px;
  }
  .card--front .brand { height: 290px; }
  .brand__dot {
    width: 18px; height: 18px; border-radius: 50%;
    background: var(--green);
  }
  .brand__name {
    font-weight: 700; font-size: 38px; color: var(--turquoise);
    letter-spacing: 0.5px;
  }

  .divider {
    position: absolute; left: 360px; width: 2px;
    background: linear-gradient(to bottom, transparent, var(--rule), transparent);
  }
  .card--back .divider { top: 40px; height: 340px; }
  .card--front .divider { top: 40px; height: 220px; }

  .pitch {
    position: absolute; left: 392px; top: 50px; right: 34px;
    font-size: 17px; line-height: 1.45;
  }
  .pitch p + p { margin-top: 10px; }
  .pitch strong { font-weight: 700; }

  .contacts {
    position: absolute; left: 392px; top: 70px;
    list-style: none;
    font-size: 22px;
  }
  .contacts li { display: flex; align-items: center; gap: 12px; margin-bottom: 16px; }
  .contacts svg { width: 22px; height: 22px; flex: none; }

  .web-band {
    position: absolute; left: 0; right: 0; top: 298px; height: 72px;
    background: var(--turquoise);
    border-top: 10px solid var(--card);
    box-shadow: 0 -1px 0 0 var(--green);
    display: flex; align-items: center; padding-left: 200px;
  }
  .web-band__url {
    color: #fff; font-size: 24px; font-weight: 600; letter-spacing: 2px;
  }
  .web-band__edge {
    position: absolute; left: 0; right: 0; bottom: -14px; height: 2px;
    background: var(--green);
  }
</style>
</head>
<body>
<main class="stage">

  <section class="card card--back" aria-label="Card back">
    <div class="brand">
      <span class="brand__dot"></span>
      <span class="brand__name">Morven Lisk</span>
    </div>
    <div class="divider"></div>
    <div class="pitch">
      <p>Do you struggle to switch off?<br>
      Want to be healthier and feel fitter?<br>
      Want closer relationships?<br>
      More clarity over the direction you are headed?</p>
      <p>I can help you do these things using integrated mind-body techniques.</p>
      <p>Visit <strong>morvenlisk.co.uk</strong> TODAY to apply for a FREE Breakthrough session.</p>
    </div>
  </section>

  <section class="card card--front" aria-label="Card front">
    <div class="brand">
      <span class="brand__dot"></span>
      <span class="brand__name">Morven Lisk</span>
    </div>
    <div class="divider"></div>
    <ul class="contacts">
      <li>
        <svg viewBox="0 0 24 24" aria-hidden="true"><circle cx="12" cy="12" r="10.5" fill="none" stroke="#0aa3c7" stroke-width="2"/><path d="M9 7l2 3-1.2 1.2a7 7 0 0 0 3 3L14 13l3 2-1.2 2c-4 0-8.8-4.8-8.8-8.8z" fill="#0aa3c7"/></svg>
        <span>+44 7915 302618</span>
      </li>
      <li>
        <svg viewBox="0 0 24 24" aria-hidden="true"><rect x="2" y="5" width="20" height="14" rx="2" fill="#0aa3c7"/><path d="M3 6l9 7 9-7" fill="none" stroke="#fff" stroke-width="1.8"/></svg>
        <span>morven@morvenlisk.co.uk</span>
      </li>
      <li>
        <svg viewBox="0 0 24 24" aria-hidden="true"><circle cx="12" cy="12" r="10" fill="#0aa3c7"/></svg>
        <span>morvenlisk</span>
      </li>
    </ul>
    <div class="web-band">
      <span class="web-band__url">www.morvenlisk.co.uk</span>
      <span class="web-band__edge"></span>
    </div>
  </section>

</main>
</body>
</html>
```